Brightwell Counseling Business Card Design Project

I am starting a new business that provides counseling and coaching services to individuals and couples. These individuals are people looking to "transform" or grow in the personal lives. The design should convey trust, intimacy, hope, growth. It should be professional, elegant.
Contact information
Name: Dana R. Holcomb
Title: Counselor and Life Coach
Slogan: Bringing Hope. Transforming Lives.
address: 40917 Ridgecrest Road, Suite 300
Plymouth, MN 55392
Phone: 763-804-7719
Email: dana@brightwell-kx.example
website: www.brightwell-kx.example
Back side of card should have bullets:
Individual counseling
Relationship counseling
Life Coaching for Teens and Adults
Group Workshops

```html
<!DOCTYPE html>
<html lang="en">
<head>
<meta charset="utf-8">
<title>Brightwell Counseling Business Cards</title>
<link href="https://fonts.googleapis.com/css2?family=Open+Sans:ital,wght@0,400;0,600;0,700;1,400&display=swap" rel="stylesheet">
<style>
  :root {
    --backdrop: #e9e6e2;
    --card: #ffffff;
    --navy: #1d3f6e;
    --brand-blue: #2f7fb8;
    --slate: #5a5a5a;
    --ink: #222222;
    --band-grey: #4d4d4d;
    --rule: #c9d6e3;
  }
  * { box-sizing: border-box; margin: 0; padding: 0; }
  html, body { width: 1200px; height: 475px; overflow: hidden; }
  body {
    background: var(--backdrop);
    font-family: "Open Sans", Arial, sans-serif;
    position: relative;
  }
  .card {
    position: absolute;
    background: var(--card);
    box-shadow: 0 3px 10px rgba(0,0,0,0.25);
  }
  .card--front { left: 72px; top: 93px; width: 525px; height: 299px; }
  .card--back { left: 627px; top: 91px; width: 508px; height: 297px; }

  .edge-band { position: absolute; left: 0; top: 0; width: 16px; height: 299px; }

  .brand { display: flex; align-items: center; gap: 10px; position: absolute; }
  .brand__dot {
    width: 30px; height: 30px; border-radius: 50%;
    background: var(--brand-blue);
  }
  .brand__name {
    font-weight: 600; font-size: 25px; color: var(--brand-blue);
    letter-spacing: 0.5px; white-space: nowrap;
  }
  .card--front .brand { left: 32px; top: 50px; }
  .card--back .brand { left: 0; right: 0; top: 58px; justify-content: center; }

  .contact {
    position: absolute; left: 27px; top: 185px;
    list-style: none; color: var(--ink); font-size: 15px; line-height: 21px;
  }
  .contact__item { display: flex; align-items: center; gap: 6px; }
  .contact__icon { width: 11px; height: 11px; flex: none; }
  .contact__address { font-size: 13.5px; line-height: 19px; margin-top: 2px; }

  .holder {
    position: absolute; right: 22px; top: 185px; text-align: right;
  }
  .holder__name { font-weight: 700; font-size: 17px; line-height: 22px; color: var(--navy); }
  .holder__title { font-size: 12.5px; line-height: 18px; color: var(--slate); margin-top: 2px; }

  .slogan {
    position: absolute; left: 0; right: 0; top: 104px;
    text-align: center; font-style: italic; font-size: 14px; color: var(--navy);
  }
  .services {
    position: absolute; left: 70px; right: 70px; top: 146px;
    padding-top: 14px; border-top: 1px solid var(--rule);
    list-style: none; display: grid; grid-template-columns: 1fr 1fr;
    column-gap: 16px; row-gap: 6px;
    font-size: 12.5px; line-height: 17px; color: var(--ink);
  }
  .services__item { display: flex; align-items: flex-start; gap: 7px; }
  .services__item::before {
    content: ""; flex: none; width: 6px; height: 6px; margin-top: 6px;
    border-radius: 50%; background: var(--brand-blue);
  }

  .back-url {
    position: absolute; left: 0; right: 0; top: 246px;
    text-align: center; font-size: 14.5px; letter-spacing: 1.4px; color: var(--ink);
  }
  .back-url__domain { color: var(--brand-blue); }
</style>
</head>
<body>
  <section class="card card--front" aria-label="Business card front">
    <svg class="edge-band" viewBox="0 0 16 299" aria-hidden="true">
      <polygon points="0,0 16,0 16,142 0,158" fill="var(--navy)"/>
      <polygon points="0,168 16,152 16,299 0,299" fill="var(--band-grey)"/>
    </svg>
    <div class="brand">
      <span class="brand__dot"></span>
      <span class="brand__name">Brightwell Counseling</span>
    </div>
    <ul class="contact">
      <li class="contact__item">
        <svg class="contact__icon" viewBox="0 0 12 12" aria-hidden="true"><path d="M3 1 L5 3.5 L4 5 Q5 7.5 7 8 L8.5 7 L11 9 L9.5 11 Q3 10.5 1 2.5 Z" fill="var(--navy)"/></svg>
        763-804-7719
      </li>
      <li class="contact__item">
        <svg class="contact__icon" viewBox="0 0 12 12" aria-hidden="true"><rect x="0.5" y="2.5" width="11" height="7.5" fill="var(--navy)"/><path d="M0.5 2.5 L6 7 L11.5 2.5" stroke="#fff" fill="none"/></svg>
        dana@brightwell-kx.example
      </li>
      <li class="contact__item">
        <svg class="contact__icon" viewBox="0 0 12 12" aria-hidden="true"><circle cx="6" cy="6" r="5.5" fill="var(--navy)"/><path d="M0.5 6 H11.5 M6 0.5 V11.5 M6 0.5 Q2.5 6 6 11.5 M6 0.5 Q9.5 6 6 11.5" stroke="#fff" stroke-width="0.8" fill="none"/></svg>
        www.brightwell-kx.example
      </li>
      <li class="contact__address">40917 Ridgecrest Road<br>Suite 300 Plymouth, MN 55392</li>
    </ul>
    <div class="holder">
      <p class="holder__name">Dana R. Holcomb</p>
      <p class="holder__title">Counselor and Life Coach</p>
    </div>
  </section>

  <section class="card card--back" aria-label="Business card back">
    <div class="brand">
      <span class="brand__dot"></span>
      <span class="brand__name">Brightwell Counseling</span>
    </div>
    <p class="slogan">Bringing Hope. Transforming Lives.</p>
    <ul class="services">
      <li class="services__item">Individual counseling</li>
      <li class="services__item">Relationship counseling</li>
      <li class="services__item">Life Coaching for Teens and Adults</li>
      <li class="services__item">Group Workshops</li>
    </ul>
    <p class="back-url">www.<span class="back-url__domain">brightwell-kx</span>.example</p>
  </section>
</body>
</html>
```